Business Card Design

We need a design for business cards for our company. We have a logo. We teach EMT's and we are based out of Virginia. The information that will need to add would be, name, title, phone number, email, address. On the back of the business card would be "We help you, help others"

Target Market(s)

People that want to become EMT's

Colors

Designer to choose colors to be used in the design.

Requirements
Must have
• company logo

```html
<!DOCTYPE html>
<html lang="en">
<head>
<meta charset="utf-8">
<title>Crestline Training – Business Card</title>
<link href="https://fonts.googleapis.com/css2?family=Work+Sans:wght@400;500;600&display=swap" rel="stylesheet">
<style>
  :root {
    --stage: #b9b9b9;
    --navy: #222b35;
    --red: #c0202f;
    --grey: #9a9b9f;
    --text-grey: #7d7f84;
    --white: #ffffff;
  }
  * { box-sizing: border-box; margin: 0; padding: 0; }
  html, body { width: 1200px; height: 930px; overflow: hidden; }
  body {
    background: var(--stage);
    font-family: "Work Sans", Arial, sans-serif;
    position: relative;
  }
  .card {
    position: absolute;
    width: 560px;
    height: 320px;
    border-radius: 22px;
    overflow: hidden;
  }
  .card-back {
    left: 80px; top: 90px;
    background: var(--navy);
    display: flex; align-items: center; justify-content: center;
  }
  .card-front {
    left: 560px; top: 520px;
    background: var(--white);
  }
  .wave { position: absolute; inset: 0; }
  .brand {
    display: flex; align-items: center; gap: 10px;
    color: var(--red);
    font-weight: 600;
    letter-spacing: 0.5px;
    text-transform: uppercase;
  }
  .brand-dot {
    width: 14px; height: 14px; border-radius: 50%;
    background: var(--red);
  }
  .card-back .brand { font-size: 34px; }
  .card-front .brand {
    position: absolute; left: 34px; top: 200px;
    font-size: 24px;
  }
  .holder {
    position: absolute; right: 32px; top: 104px;
    text-align: right;
  }
  .holder-name {
    color: var(--red); font-size: 24px; font-weight: 500;
    letter-spacing: 0.3px; text-transform: uppercase;
  }
  .holder-title { color: var(--text-grey); font-size: 14px; margin-top: 2px; }
  .rule {
    position: absolute; height: 1.5px; background: var(--red);
  }
  .rule-name { right: 32px; top: 165px; width: 250px; }
  .rule-contact { left: 34px; top: 250px; width: 200px; }
  .address {
    position: absolute; right: 32px; top: 182px;
    text-align: right; color: var(--text-grey);
    font-size: 14px; line-height: 1.45;
  }
  .contacts {
    position: absolute; left: 34px; top: 258px;
    list-style: none; color: var(--text-grey);
    font-size: 13.5px; line-height: 19px;
  }
  .contacts li { display: flex; align-items: center; gap: 8px; }
  .contacts svg { width: 11px; height: 11px; flex: none; }
  .contacts .accent { color: var(--red); }
</style>
</head>
<body>

  <section class="card card-back" aria-label="Card back">
    <div class="brand"><span class="brand-dot"></span>Crestline Training</div>
  </section>

  <section class="card card-front" aria-label="Card front">
    <svg class="wave" viewBox="0 0 560 320" preserveAspectRatio="none" aria-hidden="true">
      <path d="M0 0H560V96C430 98 300 120 190 148C110 168 45 190 0 210Z" fill="#9a9b9f"/>
      <path d="M0 0H560V78C430 82 300 100 190 126C110 146 45 168 0 190Z" fill="#ffffff"/>
      <path d="M0 0H560V70C430 74 300 92 190 118C110 138 45 160 0 180Z" fill="#c0202f"/>
      <path d="M0 150C60 128 120 112 200 100" stroke="#ffffff" stroke-width="5" fill="none"/>
    </svg>

    <div class="brand"><span class="brand-dot"></span>Crestline Training</div>

    <div class="holder">
      <div class="holder-name">Daniel Hayes</div>
      <div class="holder-title">Director</div>
    </div>
    <div class="rule rule-name"></div>

    <address class="address" style="font-style:normal">
      418 Harbor St.<br>Riverton, VA 23220
    </address>

    <div class="rule rule-contact"></div>
    <ul class="contacts">
      <li>
        <svg viewBox="0 0 12 12" aria-hidden="true"><path d="M2.5 1l2 2.2-1 1.2a7 7 0 0 0 4 4l1.2-1 2.2 2-1.2 1.5C5 10.6 1.4 7 1 2.2Z" fill="#c0202f"/></svg>
        555-014-2760
      </li>
      <li>
        <svg viewBox="0 0 12 12" aria-hidden="true"><rect x="1" y="2.5" width="10" height="7" fill="none" stroke="#c0202f" stroke-width="1.3"/><path d="M1 3l5 3.5L11 3" fill="none" stroke="#c0202f" stroke-width="1.3"/></svg>
        info@crestlinetraining.com
      </li>
      <li>
        <svg viewBox="0 0 12 12" aria-hidden="true"><circle cx="6" cy="6" r="5" fill="none" stroke="#c0202f" stroke-width="1.2"/><path d="M1 6h10M6 1c-2 3-2 7 0 10M6 1c2 3 2 7 0 10" fill="none" stroke="#c0202f" stroke-width="1"/></svg>
        <span>www.<span class="accent">crestlinetraining</span>.com</span>
      </li>
    </ul>
  </section>

</body>
</html>
```